Website Performance Testing eBook for the software testing industry

Overview:
I would like an ebook/whitepaper designed. This ebook will be digital published on my website as a lead generation piece. The purpose is to give high level tips on what to look for and things to think about when working on a website performance testing project.
The ebook also demonstrates our expertise and knowledge on the topic.
Topic:
This is an ebook on software testing. Specifically, website performance testing.
About Veltrana:
Veltrana Solutions is an outsourcing development and software testing firm, and we provide expert services for application development, testing and data analytics. We extend our clients’ software testing capabilities with on-demand technical expertise. Our quality assurance resources work as part of our clients’ teams to help test applications on time and within budget.
Our model is designed to allocate the right mix of local and offshore resources in order to optimize expertise, speed and cost. We provide the ability to quickly add specialty skills to our client’s development team without them incurring long-term costs. The result is far better management of resource capacities and outcomes.
Background on our branding and previous pieces:
I have included a few of our previous ebooks and whitepapers. I like the look and feel of these pieces, however we have made updates to our brand guidelines since them, so the new brand guidelines will need to be incorporated, and I'd like to refresh/update what we have done in the past.
Refer to our website for an idea of our look and feel. This page is one of our newer sections and would be a good reference:
http://www.veltranasol.example/data-analytics/
Tone and feel:
- The look and feel should be professional, clean and polished.
- I like good use of whitespace.
- I would prefer to keep stock photography of people to a minimum. Any images should add to the content and be relevant to the content.
(Also, I uploaded some InDesign files in case you wanted to refer to those assets, but I didn't include the Links folder because they were too big. If there's anything you more you need, let me know)
Target Market(s)
Audience:
The audience is senior Quality Assurance and Software Testing professionals.
- 30-45 years old
- Technical mindset
- Interested in learning
Titles include
- QA Lead
- QA Manager
- QA Director
- Director or VP of Development
- QA Automation Engineer
Our customers are medium to large sized companies. Many are software companies, but many are also enterprises in all almost all industries.

```html
<!DOCTYPE html>
<html lang="en">
<head>
<meta charset="utf-8">
<title>Website Performance Testing – Do's and Don'ts</title>
<link href="https://fonts.googleapis.com/css2?family=Open+Sans:wght@300;400;600;700&display=swap" rel="stylesheet">
<style>
  :root {
    --brand-red: #e8432f;
    --text-grey: #555555;
    --header-grey: #5a5a5a;
    --rule-grey: #d4d4d4;
    --ink: #222222;
    --paper: #ffffff;
  }
  * { margin: 0; padding: 0; box-sizing: border-box; }
  html, body { width: 927px; height: 1200px; overflow: hidden; background: var(--paper); }
  body { font-family: "Open Sans", Arial, sans-serif; position: relative; color: var(--text-grey); }

  .page-header { position: absolute; left: 54px; top: 64px; width: 818px; height: 45px; border-bottom: 1px solid var(--rule-grey); }
  .doc-title { position: absolute; left: 0; top: 9px; font-size: 13px; font-weight: 400; color: var(--header-grey); }
  .brand-name { position: absolute; right: 10px; top: 0; font-size: 24px; font-weight: 400; color: var(--brand-red); letter-spacing: -0.3px; }

  .section-title { position: absolute; left: 98px; top: 166px; height: 106px; border-left: 2px solid var(--brand-red); padding-left: 28px; padding-top: 13px; }
  .section-title h1 { font-weight: 300; font-size: 39px; line-height: 38px; color: var(--brand-red); letter-spacing: -0.3px; text-transform: uppercase; }

  .intro { position: absolute; left: 110px; top: 322px; font-size: 14.5px; font-weight: 300; color: var(--text-grey); }

  .list-band { position: absolute; left: 0; top: 396px; width: 282px; height: 13px; background: var(--brand-red); }
  .list-label { position: absolute; left: 310px; top: 393px; font-size: 14px; font-weight: 600; color: var(--ink); }

  .tip { position: absolute; left: 164px; width: 670px; font-size: 14.5px; line-height: 21.6px; font-weight: 300; color: var(--text-grey); }
  .tip::before { content: ""; position: absolute; left: -67px; top: 5px; width: 11px; height: 11px; border-radius: 50%; background: var(--brand-red); }
  .tip strong { font-weight: 600; color: #444444; }

  .page-number { position: absolute; left: 818px; top: 1124px; font-size: 15px; font-weight: 300; color: var(--brand-red); }
</style>
</head>
<body>
  <header class="page-header">
    <span class="doc-title">Website Performance Testing</span>
    <span class="brand-name">Veltrana</span>
  </header>

  <div class="section-title">
    <h1>The Do’s and Don’ts of Website<br>Performance Testing</h1>
  </div>

  <p class="intro">When it is time to implement the test plan, avoid common strategic and tactical pitfalls:</p>

  <div class="list-band"></div>
  <div class="list-label">DO</div>

  <p class="tip" style="top:459px"><strong>Do</strong> keep your in-house test infrastructure up-to-date even if you use cloud-based testing. It is your baseline environment for isolating cloud-based testing side-effects, which will drastically reduce the time for root cause analysis for many defects.</p>
  <p class="tip" style="top:567px"><strong>Do</strong> use your live site, if one exists, to guide load and stress testing parameters on the developing site. For example, an initial test load might be the number of actual peak-hours orders multiplied by your expected growth rate plus 20 percent overhead.</p>
  <p class="tip" style="top:676px"><strong>Do</strong> track both client and server-side traffic during non-peak and peak performance testing to determine ratios between traffic and processing activities, which often discovers imbalances.</p>
  <p class="tip" style="top:772px"><strong>Do</strong> test as many pages and combinations of page traversals as possible. Measure single page and page combination load times down to the component level.</p>
  <p class="tip" style="top:867px"><strong>Do</strong> pay attention to which pages or activities are consuming an inordinate amount of time relative to other areas of the website. This helps optimize use of your test and repair resources.</p>
  <p class="tip" style="top:962px"><strong>Do</strong> distribute generated loads geographically and by network segment.</p>

  <div class="page-number">4</div>
</body>
</html>
```